Brevard Trade Partners - we are Asian sourcing agents

We are sourcing agents based in the USA and we act as sourcing agents for clients in throughout the world. We focus primarily on custom sewn goods. So basically companies who do not have the in-house expertise to do it themselves, come to us and have us find suitable factories in Asia to do the production. We are middlemen. We find the factories...quote the project...manage the quality control and then deliver the goods directly to our customer's door. We pride ourselves in making the communication very easy and precise.

Current page is www.brevardtradepartners.com

I am not happy w/ the overall look. The spacing...the photos, the fonts...the design elements...the pictures. I want a cool, crisp design that conveys professionalism and clearly depicts/explains what we do.

Requirements
Must have
• use my logo....I like it...it was designed by someone on this website.
Nice to have
• a video/animation of the entire process would be wonderful. Showing initial contact with our office in the USA...then to my correspondence with my offices in Taiwan and in Hong Kong...and then back and fort w/ the customer.....and then between my people in Hong Kong/Taiwan with the local factories......and then a quote is generated and sent to my client......to samples being made and sent for approval.....to a PO being generated......to final samples being sent.....to the order being shipped and delivered to the clients warehouse. I was thinking of an animation showing arrows and text showing the back and forth communication and explaining how the process flows.

```html
<!DOCTYPE html>
<html lang="en">
<head>
<meta charset="utf-8">
<title>Brevard Trade Partners – Asian Sourcing Agents</title>
<link rel="stylesheet" href="https://fonts.googleapis.com/css2?family=PT+Sans:wght@400;700&family=Open+Sans:wght@400;600&display=swap">
<style>
:root{
  --green:#7fae12;
  --green-dark:#5b8a08;
  --green-deep:#4a7206;
  --ink:#2a2a2a;
  --text:#555;
  --muted:#777;
  --band:#efefef;
  --footer:#2e2e2e;
  --white:#fff;
}
*{box-sizing:border-box;margin:0;padding:0}
html,body{width:1200px;height:2211px;overflow:hidden;background:var(--white)}
body{position:relative;font-family:"Open Sans",sans-serif;color:var(--text)}
.abs{position:absolute}
h1,h2,h3,h4{font-family:"PT Sans",sans-serif;font-weight:400;color:var(--ink)}
h2 em,h3 em{font-style:normal;color:var(--green)}

/* header */
.site-header{left:0;top:0;width:1200px;height:121px}
.brand{left:99px;top:34px;display:flex;align-items:center;gap:10px;font-family:"PT Sans",sans-serif;font-weight:700;font-size:27px;color:var(--green-deep);letter-spacing:.5px}
.brand-mark{width:16px;height:16px;background:var(--green-deep)}
.main-nav{right:99px;top:61px;display:flex;gap:35px;font-family:"PT Sans",sans-serif;font-size:15px;color:#333}
.main-nav .active{color:var(--green)}

/* hero */
.hero{left:0;top:121px;width:1200px;height:473px;background:linear-gradient(180deg,#8fb7d9 0%,#c9dbea 45%,#7d8a97 72%,#4a5260 100%)}
.hero-caption{left:99px;top:287px;width:354px;height:179px;background:rgba(40,45,55,.72);padding:22px 16px}
.hero-caption .kicker{font-family:"PT Sans",sans-serif;font-size:20px;color:#fff}
.hero-caption .headline{font-family:"PT Sans",sans-serif;font-weight:700;font-size:37px;color:#fff;line-height:1.15}
.hero-caption p{font-size:11.5px;color:#fff;line-height:1.35;margin-top:4px}
.dots{display:flex;gap:8px;margin-top:14px}
.dots span{width:11px;height:11px;border-radius:50%;background:#bbb}
.dots span:first-child{background:var(--green)}

.quote{left:805px;top:121px;width:296px;height:495px;background:linear-gradient(180deg,#8cbc16,#6c9c0c);padding:24px 18px 0 18px}
.quote h3{font-weight:700;font-size:30px;color:#fff}
.quote p{font-size:11.5px;color:#fff;line-height:1.35;margin:8px 0 12px}
.field{background:#fff;height:48px;margin:0 4px 6px 4px;padding:14px 12px;font-size:12px;color:#333}
.field.msg{height:108px}
.btn-submit{display:inline-block;margin-top:12px;background:#111;color:#fff;font-size:12px;padding:9px 18px;border-radius:3px}
.fold{left:782px;top:594px}

/* welcome */
.photo{background:linear-gradient(135deg,#c7c2bb,#9a3a3a 60%,#c41e2b);border:5px solid #fff;box-shadow:0 0 0 1px #ddd,0 2px 6px rgba(0,0,0,.15)}
.welcome-photo{left:99px;top:644px;width:274px;height:238px}
.welcome{left:400px;top:638px;width:385px}
.welcome h2,.how h2{font-size:32px}
.welcome p{font-size:11.5px;line-height:1.8;margin-top:14px;color:#444}
.btn{display:inline-block;background:linear-gradient(180deg,#8cbc16,#5f8f08);color:#fff;font-size:12px;padding:8px 12px;border-radius:3px}
.welcome .btn{margin-top:12px}
.how{left:811px;top:638px;width:290px}
.video{left:811px;top:688px;width:290px;height:192px;background:linear-gradient(135deg,#d9d4cc,#5a5a5a 70%,#2f2f2f)}

/* categories */
.cat-title{left:99px;top:928px;font-size:32px}
.pager{left:1029px;top:937px;display:flex;gap:3px}
.pager span{width:35px;height:39px;background:#111;color:#fff;display:flex;align-items:center;justify-content:center;font-size:16px}
.card{top:1002px;width:238px;height:398px;background:#fff;box-shadow:inset 0 0 40px rgba(0,0,0,.12);padding:0 23px}
.card .thumb{width:192px;height:160px;margin:20px auto 0;background:radial-gradient(circle,#c9cfd8,#eef0f2 70%)}
.card h3{font-size:25px;color:var(--green);margin-top:40px}
.card p{font-size:11.5px;line-height:1.75;color:#555;margin-top:10px}
.card .btn{margin-top:16px}

/* info columns */
.col{top:1468px}
.col h3{font-size:31px}
.sport-photo{left:99px;top:1533px;width:289px;height:137px;background:linear-gradient(90deg,#ededed,#b7282e 30%,#222 50%,#b7282e 70%,#ededed)}
.sport-text{left:97px;top:1684px;width:290px;font-size:11.5px;line-height:1.8;color:#444}
.links{list-style:none;margin-top:26px}
.links li{font-size:13px;color:#555;line-height:31px;padding-left:24px;position:relative}
.links li::before{content:"";position:absolute;left:2px;top:12px;border-left:5px solid var(--green);border-top:4px solid transparent;border-bottom:4px solid transparent}

/* footer links */
.band{left:0;top:1794px;width:1200px;height:343px;background:var(--band)}
.fcol{top:1830px}
.fcol h4{font-size:24px;margin-bottom:12px}
.fcol ul{list-style:none}
.fcol li{font-size:12px;line-height:20.6px;color:#555}
.fcol h4.second{margin-top:20px}

.bottom{left:0;top:2137px;width:1200px;height:74px;background:var(--footer)}
.copy{left:97px;top:2164px;font-size:12px;color:#bbb}
.social{left:900px;top:2162px;display:flex;gap:6px}
.social span{width:26px;height:26px;border-radius:50%;background:#777}
</style>
</head>
<body>

<header class="site-header abs">
  <div class="brand abs"><span class="brand-mark"></span>Brevard Trade Partners</div>
  <nav class="main-nav abs">
    <span class="active">Home</span><span>Product</span><span>Categories</span><span>About Us</span><span>Request Quote</span>
  </nav>
</header>

<section class="hero abs" role="img" aria-label="City skyline with a broadcast tower along a river"></section>
<div class="hero-caption abs">
  <div class="kicker">USA helping to</div>
  <div class="headline">outsource asian</div>
  <p>We aren't tied to a particular sewing factory in China, India, Korea, Vietnam, &amp; Thailand.</p>
  <div class="dots"><span></span><span></span><span></span></div>
</div>

<svg class="fold abs" width="23" height="22" viewBox="0 0 23 22"><polygon points="0,0 23,0 23,22" fill="#4e7a06"/></svg>
<form class="quote abs">
  <h3>Request a Quote</h3>
  <p>Please contact us for immediate consultation regarding your outsourcing project.</p>
  <div class="field">Name</div>
  <div class="field">Email*</div>
  <div class="field">Phone</div>
  <div class="field msg">Message</div>
  <span class="btn-submit">Submit</span>
</form>

<div class="photo welcome-photo abs" role="img" aria-label="Sewing machine stitching red fabric"></div>
<section class="welcome abs">
  <h2>Welcome to <em>brevardtradepartners</em></h2>
  <p>We outsource sewing services direct from China. Our long-established and extensive network of offshore factory-partners provides our clients with access to a wide variety of contract sewing expertise from Chinese manufacturers.</p>
  <p>Clients only need to communicate with our US agents, but will have the benefits of the cost savings...</p>
  <span class="btn">Read More</span>
</section>
<section class="how abs"><h2>How it <em>Works</em></h2></section>
<div class="photo video abs" role="img" aria-label="Video of a factory worker at a sewing machine">
  <svg width="280" height="182" viewBox="0 0 280 182"><circle cx="140" cy="91" r="15" fill="none" stroke="#fff" stroke-width="3"/><polygon points="135,82 135,100 149,91" fill="#fff"/></svg>
</div>

<h2 class="cat-title abs">Our <em>Categories</em></h2>
<div class="pager abs"><span>‹</span><span>›</span></div>

<article class="card abs" style="left:99px"><div class="thumb" role="img" aria-label="Blue pet harness and leash"></div><h3>Sewn Goods</h3><p>Locating sewing manufacturers in China, India, Korea, Vietnam, &amp; Thailand to quote</p><span class="btn">Read More</span></article>
<article class="card abs" style="left:354px"><div class="thumb" role="img" aria-label="Black and red messenger bag"></div><h3>Bags</h3><p>Locating sewing manufacturers in China, India, Korea, Vietnam, &amp; Thailand to quote</p><span class="btn">Read More</span></article>
<article class="card abs" style="left:609px"><div class="thumb" role="img" aria-label="Pair of black and white winter gloves"></div><h3>Gloves</h3><p>Locating sewing manufacturers in China, India, Korea, Vietnam, &amp; Thailand to quote</p><span class="btn">Read More</span></article>
<article class="card abs" style="left:863px"><div class="thumb" role="img" aria-label="Navy motorcycle cover"></div><h3>Covers</h3><p>Locating sewing manufacturers in China, India, Korea, Vietnam, &amp; Thailand to quote</p><span class="btn">Read More</span></article>

<section class="col abs" style="left:99px"><h3>Sporting <em>Goods</em></h3></section>
<div class="sport-photo abs" role="img" aria-label="Row of red and black golf bags"></div>
<p class="sport-text abs">Brevard Trade Partners has been sourcing custom sewn goods in Asia since 1998. We work with our clients by matching their unique production needs with the best possible</p>

<section class="col abs" style="left:462px">
  <h3>Sourcing <em>Solutions</em></h3>
  <ul class="links"><li>Bags</li><li>Cases</li><li>Covers</li><li>Gloves</li><li>Medical</li><li>Sewn Goods</li><li>Sporting Goods</li></ul>
</section>
<section class="col abs" style="left:778px">
  <h3>What You Need <em>to Know</em></h3>
  <ul class="links"><li>Contract Sewing in China</li><li>What is the Process?</li><li>What the Minimum Order?</li><li>Contract Outsourcing FAQ</li><li>Outsourcing Case Study</li><li>Custom Industrial Sewing in China</li></ul>
</section>

<div class="band abs"></div>
<section class="fcol abs" style="left:97px"><h4>Custom Bags</h4><ul><li>Athletic Bags</li><li>Backpacks</li><li>Computer Bags</li><li>Cooler Bags</li><li>Cosmetic Bags</li><li>Handbags</li><li>Messenger Bags</li><li>Shopping Bags</li><li>Tool Bags</li><li>Travel Bags</li><li>Yoga Bags</li></ul></section>
<section class="fcol abs" style="left:320px"><h4>Custom Covers</h4><ul><li>ATV Covers</li><li>Chair Covers</li><li>Equipment Covers</li><li>Golf Cart Covers</li><li>Motorcycle Covers</li><li>Outdoor Furniture Covers</li><li>Outdoor Grill Cover</li><li>Personal Watercraft Covers</li><li>Snowmobile Covers</li></ul></section>
<section class="fcol abs" style="left:603px"><h4>Medical Accessories</h4><ul><li>Medical Equipment Covers</li><li>Medical Pads</li><li>Medical Sheets &amp; Bedding Supplies</li><li>Oxygen Tank Cases and Bags</li></ul><h4 class="second">Custom Cases</h4><ul><li>Cosmetic Cases</li><li>Phone Cases</li><li>Tool Bags and Tool Cases</li></ul></section>
<section class="fcol abs" style="left:939px"><h4>Custom Gloves</h4><ul><li>Batting Gloves</li><li>Garden Gloves</li><li>Mechanic Gloves</li><li>Safety Gloves</li><li>Ski Gloves</li></ul></section>

<footer class="bottom abs"></footer>
<p class="copy abs">© 2015 Brevard Trade Partners, LLC.</p>
<div class="social abs"><span></span><span></span><span></span><span></span><span></span><span></span></div>

</body>
</html>
```